Business Card Design for Training Business

Clear Path Coaching is a new business that delivers training and other services with a focus on topics related to mental health and wellbeing, for example, Wellmind Response Course, Resilience etc. We have a strong focus on evidence-based psychology and neuroscience. I have a logo which I will upload with the brief, so please consider colours that work well with the logo.
Target Market(s)
Adults, workplaces (particularly government and not-for-profits)
Industry/Entity Type
Business
Contact Information for Business Card
Head Strong TrainingSamantha SellwoodDirector0438 770 850sam@headstrongtraining.com.auwww.headstrongtraining.com.au

```html
<!DOCTYPE html>
<html lang="en">
<head>
<meta charset="utf-8">
<title>Clear Path Coaching – Business Cards</title>
<link href="https://fonts.googleapis.com/css2?family=Arimo:wght@400;700&display=swap" rel="stylesheet">
<style>
  :root {
    --backdrop: #3b3430;
    --card: #1c1c1d;
    --teal: #25b9bf;
    --logo-grey: #8a8c8f;
    --text-light: #f2f2f2;
  }
  * { margin: 0; padding: 0; box-sizing: border-box; }
  html, body { width: 1200px; height: 787px; overflow: hidden; }
  body {
    background: var(--backdrop);
    font-family: "Arimo", Arial, sans-serif;
    position: relative;
  }
  .card {
    position: absolute;
    top: 238px;
    width: 540px;
    height: 310px;
    background: var(--card);
    border-radius: 3px;
    box-shadow: 0 6px 18px rgba(0,0,0,0.35);
  }
  .card--front { left: 40px; }
  .card--back { left: 620px; }

  .brand {
    position: absolute;
    left: 0; right: 0;
    display: flex;
    flex-direction: column;
    align-items: center;
  }
  .brand__mark { display: block; }
  .brand__name {
    margin-top: 10px;
    font-size: 22px;
    font-weight: 400;
    letter-spacing: 4px;
    text-transform: uppercase;
    color: var(--logo-grey);
  }
  .card--front .brand { top: 62px; }
  .card--back .brand { top: 34px; }

  .front__web {
    position: absolute;
    left: 0; right: 0;
    bottom: 58px;
    text-align: center;
    font-size: 15px;
    letter-spacing: 0.5px;
    color: var(--text-light);
  }

  .contact {
    position: absolute;
    left: 0; right: 0;
    top: 160px;
    text-align: center;
    color: var(--text-light);
  }
  .contact__name {
    font-size: 24px;
    font-weight: 700;
    color: var(--teal);
  }
  .contact__role {
    margin-top: 4px;
    font-size: 15px;
  }
  .contact__lines {
    margin-top: 14px;
    font-size: 14px;
    line-height: 1.6;
  }
  .contact__lines span + span { margin-left: 10px; }
</style>
</head>
<body>
  <section class="card card--front" aria-label="Business card front">
    <div class="brand">
      <svg class="brand__mark" width="84" height="84" viewBox="0 0 84 84" aria-hidden="true">
        <circle cx="42" cy="42" r="39" fill="none" stroke="#25b9bf" stroke-width="3"/>
      </svg>
      <div class="brand__name">Clear Path Coaching</div>
    </div>
    <div class="front__web">www.clearpathcoaching.example.au</div>
  </section>

  <section class="card card--back" aria-label="Business card back">
    <div class="brand">
      <svg class="brand__mark" width="72" height="72" viewBox="0 0 72 72" aria-hidden="true">
        <circle cx="36" cy="36" r="33" fill="none" stroke="#25b9bf" stroke-width="3"/>
      </svg>
      <div class="brand__name">Clear Path Coaching</div>
    </div>
    <div class="contact">
      <div class="contact__name">Rebecca Tanfield</div>
      <div class="contact__role">Director</div>
      <div class="contact__lines">
        <div><span>P : 0491 362 517</span><span>E : bec@clearpathcoaching.example.au</span></div>
        <div>W : www.clearpathcoaching.example.au</div>
      </div>
    </div>
  </section>
</body>
</html>
```